Business Card Design Project

Business Card
We are rebranding with a new logo
Industry/Entity Type
Business
Contact Information for Business Card
Dennis Morvale +61 487215963 dennis@quorv.com.au P.O. Box 872 Fernlow QLD 4309
Requirements
Must have
- Logo

```html
<!DOCTYPE html>
<html lang="en">
<head>
<meta charset="utf-8">
<title>Quorv International – Business Card</title>
<link rel="stylesheet" href="https://fonts.googleapis.com/css2?family=PT+Sans:wght@400;700&display=swap">
<style>
  :root {
    --page-bg: #2b2b2b;
    --card-white: #f4f4f4;
    --brand-blue: #0b79ab;
    --brand-blue-light: #14a4db;
    --brand-blue-dark: #0a5f86;
    --brand-orange: #ef8a1e;
    --text-light: #ffffff;
  }
  * { margin: 0; padding: 0; box-sizing: border-box; }
  html, body {
    width: 1200px;
    height: 915px;
    overflow: hidden;
    background: var(--page-bg);
    font-family: "PT Sans", Arial, sans-serif;
  }
  .card {
    position: absolute;
    left: 100px;
    top: 170px;
    width: 1000px;
    height: 575px;
    background: var(--card-white);
    overflow: hidden;
  }
  .card-wave {
    position: absolute;
    inset: 0;
    width: 100%;
    height: 100%;
  }
  .brand {
    position: absolute;
    left: 78px;
    top: 120px;
    display: flex;
    align-items: center;
    gap: 22px;
    color: var(--brand-blue);
    font-weight: 700;
  }
  .brand-dot {
    width: 64px;
    height: 64px;
    border-radius: 50%;
    background: var(--brand-orange);
    flex: none;
  }
  .brand-name { line-height: 1; }
  .brand-name .primary {
    display: block;
    font-size: 100px;
    letter-spacing: 2px;
  }
  .brand-name .secondary {
    display: block;
    font-size: 31px;
    letter-spacing: 6px;
    margin-top: 6px;
  }
  .contact-name {
    position: absolute;
    right: 50px;
    top: 314px;
    color: var(--text-light);
    font-weight: 700;
    font-size: 32px;
    line-height: 1;
    letter-spacing: 0.3px;
  }
  .contact-address {
    position: absolute;
    right: 50px;
    top: 366px;
    color: var(--text-light);
    font-size: 25px;
    line-height: 32px;
    text-align: right;
  }
  .contact-list {
    position: absolute;
    right: 46px;
    top: 438px;
    list-style: none;
    color: var(--text-light);
    font-size: 25px;
    line-height: 33px;
  }
  .contact-list li {
    display: flex;
    justify-content: flex-end;
    align-items: center;
    gap: 14px;
  }
  .contact-icon {
    width: 22px;
    height: 22px;
    flex: none;
  }
</style>
</head>
<body>
  <main class="card">
    <svg class="card-wave" viewBox="0 0 710 408" preserveAspectRatio="none" aria-hidden="true">
      <defs>
        <radialGradient id="blueGlow" cx="0.6" cy="0.8" r="0.75">
          <stop offset="0" stop-color="var(--brand-blue-light)"/>
          <stop offset="0.6" stop-color="var(--brand-blue)"/>
          <stop offset="1" stop-color="var(--brand-blue-dark)"/>
        </radialGradient>
      </defs>
      <path d="M0,318 C100,378 210,385 330,322 C430,240 520,132 710,118 L710,128 C525,142 440,250 340,332 C215,398 95,385 0,336 Z" fill="var(--brand-orange)"/>
      <path d="M0,346 C105,395 225,395 345,335 C445,255 535,148 710,134 L710,408 L0,408 Z" fill="url(#blueGlow)"/>
    </svg>

    <div class="brand" aria-label="Quorv International">
      <span class="brand-dot"></span>
      <span class="brand-name">
        <span class="primary">QUORV</span>
        <span class="secondary">INTERNATIONAL</span>
      </span>
    </div>

    <h1 class="contact-name">DENNIS MORVALE</h1>
    <p class="contact-address">P.O. Box 872<br>Fernlow QLD 4309</p>

    <ul class="contact-list">
      <li>+61 487215963
        <svg class="contact-icon" viewBox="0 0 24 24" aria-label="Phone"><path fill="#fff" d="M3 8c0-3 4-4 9-4s9 1 9 4v2h-5V8H8v2H3zM7 11h10l3 8H4z"/><circle cx="12" cy="15" r="2" fill="var(--brand-blue)"/></svg>
      </li>
      <li>dennis@quorv.com.au
        <svg class="contact-icon" viewBox="0 0 24 24" aria-label="Email"><rect x="3" y="6" width="18" height="12" fill="#fff"/><path d="M3 6l9 7 9-7" fill="none" stroke="var(--brand-blue)" stroke-width="1.5"/></svg>
      </li>
      <li>www.quorv.com.au
        <svg class="contact-icon" viewBox="0 0 24 24" aria-label="Website"><circle cx="12" cy="12" r="9" fill="#fff"/><path d="M3 12h18M12 3c-4 4-4 14 0 18M12 3c4 4 4 14 0 18" fill="none" stroke="var(--brand-blue)" stroke-width="1.3"/></svg>
      </li>
    </ul>
  </main>
</body>
</html>
```